Kestrel Facilities Business Card Design

We would now like to design business cards with the new Kestrel Facilities logo

Target Market(s)

Professional

Industry/Entity Type

Professional services

Contact Information for Business Card

Employee name, title, phone number, email address, corporate office address and logo.

Font styles to use
Sans Serif

Colors
0054AA
0677BA
7BADD7
CADEEF
E8F1F8

Requirements
Must have
• My logo
Should not have
• any other pictures or images besides my logo

```html
<!DOCTYPE html>
<html lang="en">
<head>
<meta charset="utf-8">
<title>Kestrel Facilities Business Card</title>
<link rel="stylesheet" href="https://fonts.googleapis.com/css2?family=Montserrat:wght@700&family=Josefin+Sans:wght@400;600&display=swap">
<style>
  :root {
    --brand-blue: #3577be;
    --deep-blue: #0054aa;
    --mid-blue: #0677ba;
    --soft-blue: #7badd7;
    --pale-blue: #e8f1f8;
    --ink: #1c1c1c;
    --paper: #ffffff;
    --backdrop: #d9dadb;
  }
  * { margin: 0; padding: 0; box-sizing: border-box; }
  html, body { width: 1200px; height: 900px; overflow: hidden; }
  body {
    background: var(--backdrop);
    position: relative;
    font-family: "Josefin Sans", sans-serif;
    color: var(--ink);
  }
  .card {
    position: absolute;
    width: 560px;
    height: 320px;
    border-radius: 26px;
    box-shadow: 0 10px 24px rgba(0,0,0,0.25);
    overflow: hidden;
  }
  .card-front {
    left: 110px; top: 90px;
    background: var(--brand-blue);
    display: flex; align-items: center; justify-content: center;
  }
  .card-back {
    left: 530px; top: 490px;
    background: var(--paper);
  }
  .wordmark {
    display: flex; align-items: center; gap: 14px;
    font-family: "Josefin Sans", sans-serif;
    font-weight: 600;
    line-height: 1;
  }
  .wordmark-square { width: 30px; height: 30px; border: 5px solid currentColor; }
  .card-front .wordmark { color: var(--paper); font-size: 36px; }
  .card-back .wordmark {
    position: absolute; right: 36px; top: 44px;
    color: var(--brand-blue); font-size: 28px;
  }
  .wordmark-square.small { width: 24px; height: 24px; border-width: 4px; }
  .ghost-square {
    position: absolute; left: 70px; top: 100px;
    width: 120px; height: 120px;
    border: 14px solid var(--pale-blue);
  }
  .accent-bar {
    position: absolute; left: 0; top: 118px;
    width: 18px; height: 46px;
    background: var(--brand-blue);
  }
  .holder { position: absolute; left: 40px; top: 110px; }
  .holder-name {
    font-family: "Montserrat", sans-serif; font-weight: 700;
    font-size: 24px; color: var(--brand-blue); letter-spacing: 0.5px;
  }
  .holder-title { font-size: 19px; margin-top: 4px; }
  .address {
    position: absolute; right: 36px; top: 156px;
    text-align: right; font-size: 18px; line-height: 1.35;
  }
  .contacts {
    position: absolute; left: 40px; bottom: 30px;
    list-style: none; font-size: 19px; line-height: 1.5;
  }
  .contacts li { display: flex; align-items: center; gap: 10px; }
  .contacts svg { width: 18px; height: 18px; fill: var(--brand-blue); flex: none; }
</style>
</head>
<body>
  <section class="card card-front" aria-label="Card front">
    <div class="wordmark"><span class="wordmark-square"></span><span>Kestrel Facilities</span></div>
  </section>

  <section class="card card-back" aria-label="Card back">
    <div class="ghost-square"></div>
    <div class="accent-bar"></div>
    <div class="holder">
      <p class="holder-name">WANJIRU OTIENO</p>
      <p class="holder-title">Co-Founder</p>
    </div>
    <div class="wordmark"><span class="wordmark-square small"></span><span>Kestrel Facilities</span></div>
    <address class="address" style="font-style:normal">P.O Box 4418-00200<br>Nairobi, Kenya</address>
    <ul class="contacts">
      <li>
        <svg viewBox="0 0 24 24" aria-hidden="true"><path d="M6.6 10.8a15.1 15.1 0 0 0 6.6 6.6l2.2-2.2c.3-.3.7-.4 1-.2 1.1.4 2.3.6 3.6.6.6 0 1 .4 1 1V20c0 .6-.4 1-1 1A17 17 0 0 1 3 4c0-.6.4-1 1-1h3.5c.6 0 1 .4 1 1 0 1.3.2 2.5.6 3.6.1.3 0 .7-.2 1z"/></svg>
        <span>+254-700-41526</span>
      </li>
      <li>
        <svg viewBox="0 0 24 24" aria-hidden="true"><path d="M2 5h20v14H2z M2 5l10 8 10-8" /></svg>
        <span>info@kestrelfm.com</span>
      </li>
      <li>
        <svg viewBox="0 0 24 24" aria-hidden="true"><circle cx="12" cy="12" r="10"/></svg>
        <span>www.kestrelfm.com</span>
      </li>
    </ul>
  </section>
</body>
</html>
```